Stylish business cards for KV7

To create an appealing and professional business card design for a WOMEN Owned Construction Supply Company.
2 sided card. Incorporate brand elements, curvy, colorful, sleek and bright. No solid white background. attached samples of styles added shapes/ribbons. Want something with that WOW that looks awesome, factor. It is a new logo, so feel free to mess with logo colors in the blue and teal factors that can look good with both dark and light background. If you want to try a watermark with just the KV7, without the "Supply" that might look cool to.

Industry/Entity Type

Women owned construction supply company

Contact Information for Business Card

Name, Title, and phone number and email, web page. maybe spot for qr code.

Font styles to use
Sans Serif

Requirements
Nice to have
• would love to see colors, maybe stylish ribbon dividers or some sort of 2 or 3 tone color card that compliments logo.
Should not have
• Please do not have all white background. Do not include Home/reale state/ or building images.

```html
<!DOCTYPE html>
<html lang="en">
<head>
<meta charset="utf-8">
<title>KV7 Supply — Business Cards</title>
<link rel="stylesheet" href="https://fonts.googleapis.com/css2?family=Poppins:wght@400;500;600&display=swap">
<style>
  :root {
    --stage: #2b2b2d;
    --slate: #6b7f96;
    --silver: #e3e7ec;
    --navy: #253f5f;
    --navy-deep: #1f3654;
    --teal: #3a9cc4;
    --ink-blue: #3e5a78;
    --paper: #ffffff;
    --contact: #e6edf5;
  }
  * { margin: 0; padding: 0; box-sizing: border-box; }
  html, body { width: 1200px; height: 875px; overflow: hidden; }
  body {
    background: var(--stage);
    font-family: "Poppins", sans-serif;
    display: flex;
    align-items: center;
    justify-content: center;
    gap: 40px;
  }
  .card {
    position: relative;
    width: 540px;
    height: 310px;
    border-radius: 22px;
    overflow: hidden;
    box-shadow: 0 18px 40px rgba(0,0,0,.45);
  }
  .card-front {
    background: var(--slate);
    display: flex;
    align-items: center;
    justify-content: center;
  }
  .wordmark {
    font-weight: 500;
    letter-spacing: .02em;
    white-space: nowrap;
  }
  .card-front .wordmark { font-size: 58px; color: var(--silver); }
  .card-back { background: var(--paper); }
  .card-back .waves { position: absolute; inset: 0; }
  .card-back .wordmark {
    position: absolute;
    left: 42px;
    top: 178px;
    font-size: 40px;
    color: var(--ink-blue);
  }
  .contact {
    position: absolute;
    left: 330px;
    top: 74px;
    color: var(--contact);
    font-size: 11.5px;
    line-height: 1.45;
  }
  .contact .name {
    font-size: 17px;
    font-weight: 600;
    color: var(--teal);
    letter-spacing: .02em;
    line-height: 1.2;
  }
  .contact .title { margin-bottom: 16px; }
  .contact .address { margin-bottom: 14px; }
  .contact-line { display: flex; align-items: center; gap: 8px; }
  .contact-line svg { width: 11px; height: 11px; flex: none; }
</style>
</head>
<body>
  <section class="card card-front" aria-label="Card front">
    <span class="wordmark">KV7 Supply</span>
  </section>

  <section class="card card-back" aria-label="Card back">
    <svg class="waves" viewBox="0 0 540 310" preserveAspectRatio="none" aria-hidden="true">
      <path d="M250 0 C300 60 305 150 300 215 C296 260 310 290 330 310 L540 310 L540 0 Z" fill="var(--navy)"/>
      <path d="M250 0 C300 60 305 150 300 215 C296 260 310 290 330 310 L318 310 C296 288 286 258 289 215 C295 150 290 70 240 0 Z" fill="var(--teal)"/>
      <path d="M215 0 C250 35 268 80 272 130 C262 85 240 40 200 0 Z" fill="var(--navy-deep)"/>
    </svg>

    <span class="wordmark">KV7 Supply</span>

    <div class="contact">
      <p class="name">DANIEL REYES</p>
      <p class="title">General Manager</p>
      <p class="address">48 Harbor Point Drive<br>Lakeview, NJ 07100 USA</p>
      <p class="contact-line">
        <svg viewBox="0 0 12 12" aria-hidden="true"><path d="M2.5 1h2l1 2.5-1.3 1a6.5 6.5 0 0 0 3.3 3.3l1-1.3L11 7.5v2a1.5 1.5 0 0 1-1.5 1.5A9 9 0 0 1 1 2.5 1.5 1.5 0 0 1 2.5 1z" fill="var(--contact)"/></svg>
        +1.555.010.284
      </p>
      <p class="contact-line">
        <svg viewBox="0 0 12 12" aria-hidden="true"><rect x="1" y="2.5" width="10" height="7" rx="1" fill="var(--contact)"/><path d="M1.5 3l4.5 3.5L10.5 3" stroke="var(--navy)" fill="none"/></svg>
        name@kv7supply.com
      </p>
      <p class="contact-line">
        <svg viewBox="0 0 12 12" aria-hidden="true"><circle cx="6" cy="6" r="5" fill="none" stroke="var(--contact)"/><ellipse cx="6" cy="6" rx="2" ry="5" fill="none" stroke="var(--contact)"/><path d="M1 6h10" stroke="var(--contact)"/></svg>
        www.kv7supply.com
      </p>
    </div>
  </section>
</body>
</html>
```